Sophisticated, clean website reflecting my feminine, playful side to sell my abstract art,

I need a website no more than 3 pages to showcase my paintings, a little about me and some contact info. I do abstracts so looking for something a little edgy, yet feminine and current.
Updates

Hi there, These are some artists websites that I Iike: Marnelvoss.com (I like how airy it is) peterwallombry.com garethpolvens.com (I like how it scrolls) I'll need a place for a photo ( a headshot-i do not have it yet so I'll need to be able to upload that later) as well as an area for my bio. Also, it's important that I will be able to upload any new photos and descriptions easily so it should be user friendly. Lastly, I like in a sunny place so would like to have this seem upbeat and playful as that is how i like to paint. thanks-I'm trying to upload my photos now -

Target Market(s)

ppl ages 35-70 who want large scale art for their homes

Industry/Entity Type

art

Coding

Coded - Design and coding required

Number of Pages Required

3 page

Colors

Designer to choose colors to be used in the design.

Requirements
Must have
• photos of my art, a place for my bio, be easy to reach me. tasteful-nothing too "in your face" -my clients are pretty high end and organized. They like clean lines
Nice to have
• sophisticated background, muted tones in the back-similar clean font throughout-no cursive
Should not have
• too many dark areas. Too many blocks of color. Too serious.

```html
<!DOCTYPE html>
<html lang="en">
<head>
<meta charset="utf-8">
<title>Studio Velora Abstracts</title>
<link rel="stylesheet" href="https://fonts.googleapis.com/css2?family=Cormorant+Garamond:wght@600;700&family=Poppins:wght@400;500&display=swap">
<style>
  :root {
    --paper: #f9f9f7;
    --ink: #171819;
    --tan: #b78f63;
    --frame: #c8bd95;
    --frame-light: #e4dcc4;
    --white: #ffffff;
    --text: #232323;
  }
  * { box-sizing: border-box; margin: 0; padding: 0; }
  html, body { width: 1200px; height: 2615px; overflow: hidden; }
  body {
    position: relative;
    background: var(--paper);
    font-family: "Poppins", sans-serif;
    color: var(--text);
  }
  .abs { position: absolute; }
  .serif { font-family: "Cormorant Garamond", serif; font-weight: 700; }
  .btn {
    position: absolute; background: var(--ink); color: var(--white);
    font-size: 14px; display: flex; align-items: center; justify-content: center;
  }

  /* header */
  .site-header { position: absolute; left: 0; top: 0; width: 1200px; height: 60px; background: var(--paper); z-index: 3; }
  .brand-mark {
    position: absolute; left: 60px; top: 10px; width: 77px; height: 75px;
    background: var(--ink); border: 3px solid var(--frame);
    display: flex; align-items: center; justify-content: center; text-align: center;
    color: var(--tan); font-family: "Poppins", sans-serif; font-size: 11px; font-weight: 500; line-height: 1.3;
  }
  .main-nav { position: absolute; top: 18px; left: 462px; display: flex; gap: 36px; font-size: 14px; }
  .header-icon { position: absolute; top: 19px; }

  /* hero */
  .hero {
    position: absolute; left: 0; top: 60px; width: 1200px; height: 578px;
    border-bottom-left-radius: 340px 210px; overflow: hidden;
    background:
      radial-gradient(ellipse 420px 230px at 560px 120px, rgba(120,70,160,.85), transparent 70%),
      radial-gradient(ellipse 260px 180px at 300px 180px, rgba(60,60,190,.75), transparent 70%),
      radial-gradient(ellipse 300px 200px at 900px 200px, rgba(140,100,170,.7), transparent 70%),
      radial-gradient(ellipse 240px 150px at 1050px 470px, rgba(40,40,90,.7), transparent 70%),
      radial-gradient(ellipse 200px 140px at 560px 420px, rgba(110,60,140,.55), transparent 70%),
      linear-gradient(180deg, #e8e2dc 0%, #ddd3cb 60%, #d7c9bd 100%);
  }
  .hero-title { position: absolute; left: 0; width: 1200px; top: 232px; text-align: center; color: var(--white); font-size: 50px; }
  .hero-sub { position: absolute; left: 370px; width: 460px; top: 306px; text-align: center; color: var(--white); font-size: 14px; line-height: 22px; }
  .arrow-box { position: absolute; width: 38px; height: 38px; display: flex; align-items: center; justify-content: center; }

  /* about */
  .eyebrow { position: absolute; color: var(--tan); font-size: 14px; }
  .section-title { position: absolute; font-size: 34px; color: var(--ink); }
  .about-copy { position: absolute; left: 61px; top: 812px; width: 525px; font-size: 14.5px; line-height: 22.5px; }
  .photo-frame { position: absolute; left: 632px; top: 742px; width: 300px; height: 281px; background: var(--frame-light); }
  .media { position: absolute; border-radius: 8px; }

  /* gallery */
  .card { position: absolute; width: 340px; }
  .card-art { width: 340px; height: 289px; background: var(--frame); padding: 5px; }
  .card-art div { width: 100%; height: 100%; border-radius: 6px; }
  .card-name { text-align: center; font-size: 20px; margin-top: 12px; color: var(--ink); }
  .card-price { text-align: center; font-size: 14px; font-weight: 500; color: var(--tan); margin-top: 2px; }
  .cart-badge { position: absolute; right: 6px; top: 16px; width: 32px; height: 32px; background: rgba(200,189,149,.6); display: flex; align-items: center; justify-content: center; }

  /* newsletter */
  .news-input { position: absolute; left: 300px; top: 2212px; width: 492px; height: 38px; background: var(--tan); color: var(--white); font-size: 14px; padding-left: 14px; display: flex; align-items: center; }

  /* footer */
  .site-footer {
    position: absolute; left: 0; top: 2318px; width: 1200px; height: 297px;
    background: var(--ink); border-top-right-radius: 360px 260px; color: var(--white);
  }
  .footer-brand { position: absolute; left: 0; width: 1200px; top: 60px; text-align: center; color: var(--tan); font-size: 20px; font-weight: 500; }
  .footer-nav { position: absolute; top: 146px; left: 465px; display: flex; gap: 44px; font-size: 13px; }
  .social { position: absolute; top: 185px; width: 38px; height: 38px; }
  .footer-rule { position: absolute; left: 0; top: 260px; width: 1200px; height: 1px; background: #3a3b3c; }
  .copyright { position: absolute; left: 0; width: 1200px; top: 272px; text-align: center; font-size: 13px; }
</style>
</head>
<body>

<header class="site-header">
  <div class="brand-mark">Studio<br>Velora</div>
  <nav class="main-nav"><span>My Paintings</span><span>About Me</span><span>Contact</span></nav>
  <svg class="header-icon" style="left:1076px" width="22" height="20" viewBox="0 0 22 20" fill="none" stroke="#171819" stroke-width="1.6" aria-label="Cart"><path d="M1 2h3l3 11h11l2-8H6"/><circle cx="9" cy="17" r="1.5"/><circle cx="16" cy="17" r="1.5"/></svg>
  <svg class="header-icon" style="left:1120px" width="20" height="20" viewBox="0 0 20 20" fill="none" stroke="#171819" stroke-width="2" aria-label="Search"><circle cx="8" cy="8" r="6"/><path d="M13 13l6 6"/></svg>
</header>

<section class="hero" role="img" aria-label="Abstract painting in purple, blue and cream brush strokes">
  <h1 class="hero-title serif">Studio Velora Abstracts</h1>
  <p class="hero-sub">Lorem Ipsum is simply dummy text of the printing and typesetting industry.</p>
  <div class="btn" style="left:547px;top:331px;width:112px;height:37px">Contact US</div>
  <div class="arrow-box" style="left:41px;top:236px;background:#171819">
    <svg width="12" height="20" viewBox="0 0 12 20" fill="none" stroke="#fff" stroke-width="1.8"><path d="M10 1L2 10l8 9"/></svg>
  </div>
  <div class="arrow-box" style="left:1123px;top:236px;background:#fff;border:1px solid #c8bd95">
    <svg width="12" height="20" viewBox="0 0 12 20" fill="none" stroke="#171819" stroke-width="1.8"><path d="M2 1l8 9-8 9"/></svg>
  </div>
</section>
<div class="arrow-box" style="left:581px;top:621px;background:#fff;border:1px solid #c8a882">
  <svg width="20" height="12" viewBox="0 0 20 12" fill="none" stroke="#171819" stroke-width="1.8"><path d="M1 2l9 8 9-8"/></svg>
</div>

<section class="about">
  <span class="eyebrow" style="left:62px;top:737px">About Me</span>
  <h2 class="section-title serif" style="left:61px;top:760px">Welcome To Studio Velora Abstracts</h2>
  <p class="about-copy">Lorem Ipsum is simply dummy text of the printing and typesetting industry. Lorem Ipsum has been the industry's standard dummy text ever since the 1500s, when an unknown printer took a galley of type and scrambled it to make a type specimen book. It has survived not only five centuries, but also the leap into electronic typesetting, remaining essentially unchanged. It was popularised in the 1960s with the release of Letraset sheets containing Lorem Ipsum passages,and more recently with desktop publishing software like Aldus PageMaker including versions of Lorem Ipsum.</p>
  <div class="btn" style="left:60px;top:1015px;width:106px;height:38px">Read More</div>
  <div class="photo-frame"></div>
  <div class="media" role="img" aria-label="Artist painting a canvas at an easel in a bright studio" style="left:642px;top:752px;width:280px;height:261px;background:linear-gradient(120deg,#e9e3d6 0%,#d8c9b4 45%,#a85a4a 75%,#5a3a30 100%)"></div>
  <div class="media" role="img" aria-label="Green and yellow abstract painting" style="left:890px;top:861px;width:251px;height:232px;background:radial-gradient(circle at 40% 50%,#7cc07a,#2f8d5a 55%,#d8e6cf 100%)"></div>
</section>

<section class="gallery">
  <span class="eyebrow" style="left:0;width:1200px;text-align:center;top:1172px">My Paintings</span>
  <h2 class="section-title serif" style="left:0;width:1200px;text-align:center;top:1193px">Explore The Velora Abstracts</h2>

  <article class="card" style="left:60px;top:1264px">
    <div class="card-art" role="img" aria-label="Painting of burgundy and pink roses"><div style="background:radial-gradient(circle at 40% 55%,#b07a7a,#e9e2e0 70%)"></div></div>
    <div class="cart-badge"><svg width="18" height="16" viewBox="0 0 22 20" fill="none" stroke="#fff" stroke-width="1.8"><path d="M1 2h3l3 11h11l2-8H6"/><circle cx="9" cy="17" r="1.5"/><circle cx="16" cy="17" r="1.5"/></svg></div>
    <h3 class="card-name serif">Painting Name</h3><p class="card-price">$500</p>
  </article>
  <article class="card" style="left:430px;top:1264px">
    <div class="card-art" role="img" aria-label="Painting of blue and ochre swirls"><div style="background:radial-gradient(circle at 50% 45%,#c9a657,#6b8fbf 45%,#eceae4 80%)"></div></div>
    <h3 class="card-name serif">Painting Name</h3><p class="card-price">$500</p>
  </article>
  <article class="card" style="left:801px;top:1264px">
    <div class="card-art" role="img" aria-label="Painting of rust red circular strokes"><div style="background:radial-gradient(circle at 65% 35%,#a8432a,#e8dcd3 65%)"></div></div>
    <h3 class="card-name serif">Painting Name</h3><p class="card-price">$500</p>
  </article>
  <article class="card" style="left:60px;top:1642px">
    <div class="card-art" role="img" aria-label="Painting of purple flower bursts"><div style="background:radial-gradient(circle at 45% 55%,#6e4c8e,#b7a5c9 45%,#eae6e2 85%)"></div></div>
    <h3 class="card-name serif">Painting Name</h3><p class="card-price">$500</p>
  </article>
  <article class="card" style="left:430px;top:1642px">
    <div class="card-art" role="img" aria-label="Painting of teal drips on cream"><div style="background:linear-gradient(90deg,#e6e0d6 30%,#8fc3d6 45%,#d5e6ec 100%)"></div></div>
    <h3 class="card-name serif">Painting Name</h3><p class="card-price">$500</p>
  </article>
  <article class="card" style="left:801px;top:1642px">
    <div class="card-art" role="img" aria-label="Painting of burgundy and pink roses"><div style="background:radial-gradient(circle at 40% 55%,#b07a7a,#e9e2e0 70%)"></div></div>
    <h3 class="card-name serif">Painting Name</h3><p class="card-price">$500</p>
  </article>

  <div class="btn" style="left:546px;top:2036px;width:108px;height:37px">View More</div>
</section>

<section class="newsletter">
  <div class="abs" role="img" aria-label="Leaf sprig illustration" style="left:240px;top:2142px;width:115px;height:102px;border-radius:50%;background:radial-gradient(circle,#9a9a97,rgba(249,249,247,0) 70%)"></div>
  <div class="abs" role="img" aria-label="Small leaf illustration" style="left:880px;top:2226px;width:58px;height:36px;border-radius:50%;background:radial-gradient(circle,#c9ccc9,rgba(249,249,247,0) 70%)"></div>
  <h2 class="section-title serif" style="left:0;width:1200px;text-align:center;top:2148px">Subscribe To Our Newslatter</h2>
  <div class="news-input">E-mail</div>
  <div class="btn" style="left:792px;top:2212px;width:108px;height:38px">Subscribe</div>
</section>

<footer class="site-footer">
  <div class="footer-brand">Studio Velora</div>
  <nav class="footer-nav"><span>My Paintings</span><span>About Me</span><span>Contact</span></nav>
  <div class="social" style="left:491px;background:#c8bd95" role="img" aria-label="Social link"></div>
  <div class="social" style="left:552px;background:#b78f63" role="img" aria-label="Social link"></div>
  <div class="social" style="left:611px;background:#b78f63" role="img" aria-label="Social link"></div>
  <div class="social" style="left:671px;background:#c8bd95" role="img" aria-label="Social link"></div>
  <div class="footer-rule"></div>
  <p class="copyright">Copyright 2022, Studio Velora Abstracts. All Rights Reserved.</p>
</footer>

</body>
</html>
```